Zielgruppe
Wir sind ein Vertriebsunternehmen, mit dem Ziel die klassische Finanz und den Kryptosektor zu verbinden. Unsere Zielgruppe sind Menschen zwischn 25 - 45 Jahre. Wir sind die Communty und Vertrieb der ersten rechtkonformen STO - Plattform ( Plattform für Wertpapiere im Kryptosektor)
Diese Projekt ist Teil eines Paketes, wir bitten nur Designer mit zu machen die alle benötigten Unterlagen designen können. (siehe restliche Projekte) - Gesamtvolumen: 2300€ Preisgeld
Online-Marketing Material
2 Vorlagen Social Media - (Einladung/Event, Sprüche/Information)
Banner
Präsentationsvorlagen - min unterschiedliche 8 Vorlagenseiten /Layouts.
Landingpage Layout f. Funnelsite für Webinaranmeldung mit Platz für Formular
Newsletter Layoutvorlage
Vorlage Infografik
Broschüre / E - Book Designe
Es werden nur Vorlagen benötigt mit 'LoremSum Texten' und Musterbildern. Wir möchten von allen Vorlagen die Originaldatei, uns stehen folgende Grafikprogramme zur Verfügung:
Adobe Photoshop
Adobe Illustrator
Canva
Newsletter und Landingpage Software: mailvorra.com
Unsere Akt. Designe (Designe Alt) gefällt uns von der Idee, dennoch wünschen wir es uns moderner und edler mit ein wenig 'spaceig'. - Eben die Vereinigung von Kryptowelt und klassischer Finanz.
Schriftart: Poppins
Farben lt. Logo
Aufgabenstellung
Die Landingpage Layout f. Funnelsite für Webinaranmeldung mit Platz für Formular - Die Landingpage ersetzt nicht unsere aktuelle Website - sondern dient zur Leadgenerierung im Socialmedia Bereich.

```html
<!DOCTYPE html>
<html lang="de">
<head>
<meta charset="utf-8">
<title>CopperLynx – Webinare &amp; Workshops</title>
<link href="https://fonts.googleapis.com/css2?family=Poppins:wght@400;500;600;700&display=swap" rel="stylesheet">
<style>
  :root{
    --navy:#21428f;
    --blue:#2171b4;
    --button:#1f6db0;
    --grey:#e1e1e1;
    --white:#ffffff;
    --ink:#111111;
  }
  *{margin:0;padding:0;box-sizing:border-box}
  html,body{width:1200px;height:2399px;overflow:hidden;background:var(--white)}
  body{font-family:'Poppins',sans-serif;color:var(--ink);position:relative}
  .abs{position:absolute}

  .top-bar{left:0;top:0;width:1200px;height:47px;background:var(--navy)}
  .header-photo{left:0;top:47px;width:1200px;height:162px;
    background:
      radial-gradient(ellipse 260px 120px at 180px 60px,rgba(70,85,115,.55),transparent 70%),
      radial-gradient(ellipse 220px 110px at 470px 110px,rgba(200,170,140,.45),transparent 70%),
      radial-gradient(ellipse 300px 160px at 1060px 90px,rgba(90,140,200,.55),transparent 70%),
      radial-gradient(ellipse 200px 120px at 820px 120px,rgba(235,238,242,.8),transparent 70%),
      linear-gradient(100deg,#8f9db3 0%,#c7cfdb 30%,#e4e7ec 55%,#cfd8e4 75%,#a9bdd6 100%)}
  .header-dots{left:940px;top:160px;display:flex;gap:13px}
  .header-dots span{width:31px;height:30px;background:var(--button)}
  .header-strip{left:0;top:209px;width:1200px;height:148px;background:var(--white)}
  .brand{left:104px;top:270px;font-size:20px;font-weight:700;color:var(--navy);display:flex;align-items:center;gap:8px;white-space:nowrap}
  .brand i{width:18px;height:18px;background:var(--blue);display:block}
  .header-title{left:289px;top:270px;font-size:23px;font-weight:700;color:var(--navy);letter-spacing:-.2px;white-space:nowrap}
  .header-photo-bottom{left:0;top:357px;width:1200px;height:27px;
    background:
      radial-gradient(ellipse 200px 30px at 1000px 14px,rgba(90,130,190,.5),transparent 70%),
      linear-gradient(90deg,#9ea8b7 0%,#c8ced8 40%,#dfe3e9 70%,#a8b2c2 100%)}

  .column{left:178px;top:384px;width:880px;height:2015px;background:var(--grey)}

  .intro{left:178px;top:398px;width:880px;height:451px;background:var(--white)}
  .intro-photo{left:178px;top:398px;width:453px;height:451px;
    background:
      radial-gradient(ellipse 150px 200px at 320px 260px,rgba(60,75,105,.55),transparent 70%),
      radial-gradient(ellipse 110px 170px at 420px 230px,rgba(80,100,140,.5),transparent 70%),
      radial-gradient(ellipse 80px 60px at 300px 120px,rgba(200,175,150,.45),transparent 70%),
      radial-gradient(ellipse 200px 100px at 150px 420px,rgba(215,222,232,.9),transparent 70%),
      linear-gradient(135deg,#eceef1 0%,#d4dae2 45%,#a6b2c2 80%,#c3cbd6 100%)}
  .intro-title{left:665px;top:420px;font-size:30px;font-weight:700}
  .intro-text{left:668px;top:492px;width:370px;font-size:16px;line-height:20.1px;font-weight:400}
  .btn{left:829px;top:780px;width:198px;height:48px;border-radius:6px;background:var(--button);
    color:var(--white);font-size:17px;font-weight:600;display:flex;align-items:center;justify-content:center}

  .signup{left:178px;top:868px;width:880px;height:184px;background:var(--blue)}
  .signup-title{left:236px;top:900px;font-size:50px;font-weight:700;line-height:56px;color:var(--white)}
  .signup-field{left:606px;top:960px;width:421px;height:66px;border-radius:12px;background:var(--white)}

  .feature{left:178px;top:1085px;width:880px;height:586px;border-bottom:2px solid var(--navy);
    background:
      radial-gradient(ellipse 260px 90px at 300px 40px,rgba(40,55,90,.8),transparent 70%),
      radial-gradient(ellipse 140px 120px at 520px 180px,rgba(235,225,210,.7),transparent 70%),
      radial-gradient(ellipse 260px 260px at 760px 280px,rgba(70,120,185,.65),transparent 70%),
      radial-gradient(ellipse 200px 150px at 800px 520px,rgba(40,55,90,.7),transparent 70%),
      radial-gradient(ellipse 300px 120px at 200px 560px,rgba(200,160,110,.6),transparent 70%),
      linear-gradient(120deg,#3c4a66 0%,#8a97ab 30%,#d9d6cf 55%,#b7c6db 75%,#6f82a4 100%)}
  .feature-veil{left:180px;top:1173px;width:430px;height:415px;background:rgba(235,238,242,.55)}
  .feature-brand{left:200px;top:1450px;font-size:34px;font-weight:700;color:var(--navy);display:flex;align-items:center;gap:12px}
  .feature-brand i{width:30px;height:30px;background:var(--navy);display:block}
  .feature-title{left:694px;top:1350px;font-size:70px;font-weight:700;line-height:78px;color:var(--white);letter-spacing:-1px}

  .webinar-title{left:206px;top:1714px;font-size:31px;font-weight:700}
  .webinar-text{left:206px;top:1772px;width:352px;font-size:16px;line-height:20.1px;text-align:justify}
  .webinar-text p{margin-bottom:20px}

  .benefits{left:610px;top:1694px;width:426px;height:426px;background:var(--blue);list-style:none;padding:50px 18px 0 29px}
  .benefits li{display:flex;align-items:center;gap:13px;color:var(--white);font-size:14.6px;line-height:18px;height:53.3px}
  .benefits svg{flex:0 0 22px}

  .footer{left:0;top:2153px;width:1200px;height:218px;background:var(--navy)}
</style>
</head>
<body>
  <div class="abs top-bar"></div>
  <div class="abs header-photo" role="img" aria-label="Faded photo of a hand pointing at business charts on a desk"></div>
  <div class="abs header-dots"><span></span><span></span><span></span></div>
  <div class="abs header-strip"></div>
  <div class="abs brand"><i></i>CopperLynx</div>
  <div class="abs header-title">LOREM IPSUM DOLOR SIT AMET, CONSECTETUER ADIPISCING ELIT, SED</div>
  <div class="abs header-photo-bottom" role="img" aria-label="Faded strip of the desk and chart photo"></div>

  <div class="abs column"></div>

  <section>
    <div class="abs intro"></div>
    <div class="abs intro-photo" role="img" aria-label="Photo of two businessmen looking at a tablet together"></div>
    <h2 class="abs intro-title">Lorem ipsum</h2>
    <p class="abs intro-text">Lorem ipsum dolor sit amet, consectetuer adipiscing elit, sed diam nonummy nibh euismod tincidunt ut laoreet dolore magna aliquam erat volutpat. Ut wisi Lorem ipsum dolor sit amet, consectetuer adipiscing elit, sed diam nonummy nibh euismod tincidunt ut laoreet dolore magna aliquam erat volutpat. Ut wisi enim ad minim veniam, quis nostrud exerci tation ullamcorper suscipit lobortis nisl ut aliquip ex ea commodo consequat. Duis autem vel eum iriure dolor in hendrerit in vulputate velit esse molestie consequat,</p>
    <div class="abs btn">Lorem ipsum</div>
  </section>

  <section>
    <div class="abs signup"></div>
    <h2 class="abs signup-title">Lorem ipsum<br>dolor sit</h2>
    <div class="abs signup-field"></div>
  </section>

  <section>
    <div class="abs feature" role="img" aria-label="Photo of hands with a pen and tablet over printed financial bar charts"></div>
    <div class="abs feature-veil"></div>
    <div class="abs feature-brand"><i></i>CopperLynx</div>
    <h2 class="abs feature-title">Lorem<br>ipsum<br>dolor sit</h2>
  </section>

  <section>
    <h2 class="abs webinar-title">Webinare &amp; Workshops</h2>
    <div class="abs webinar-text">
      <p>In unseren regelmäßigen Webinaren und Online-Workshops geben wir Ihnen Ein&shy;blick in unser Unternehmen und aktuelle sowie kommende Investment-Projekte.</p>
      <p>Unsere Experten verraten Tipps rund um Wertpapierhandel, Krypto Assets, Token, Wachstumschancen und informieren über Entwicklungen sowie Trends auf den aktuellen Finanzmärkten.<br>Die Teilnahme ist kostenlos.</p>
      <p>Für wen sind unsere Webinare &amp; On&shy;line-Workshops interessant?</p>
    </div>
    <ul class="abs benefits">
      <li><svg width="22" height="22" viewBox="0 0 22 22"><path d="M19 9.5A8 8 0 1 1 14.5 3.8" fill="none" stroke="#fff" stroke-width="2"/><path d="M7 10.5l3.5 3.5L19.5 4.5" fill="none" stroke="#fff" stroke-width="2.2"/></svg><span>Sie möchten sich mit dem 1×1 des Wertpapier Managements vertraut machen</span></li>
      <li><svg width="22" height="22" viewBox="0 0 22 22"><path d="M19 9.5A8 8 0 1 1 14.5 3.8" fill="none" stroke="#fff" stroke-width="2"/><path d="M7 10.5l3.5 3.5L19.5 4.5" fill="none" stroke="#fff" stroke-width="2.2"/></svg><span>Ihr Wissen rund um Bitcoin, Blockchain und Krypto-Assets soll wachsen</span></li>
      <li><svg width="22" height="22" viewBox="0 0 22 22"><path d="M19 9.5A8 8 0 1 1 14.5 3.8" fill="none" stroke="#fff" stroke-width="2"/><path d="M7 10.5l3.5 3.5L19.5 4.5" fill="none" stroke="#fff" stroke-width="2.2"/></svg><span>Sie möchten mehr über CopperLynx Investments und unsere Token erfahren</span></li>
      <li><svg width="22" height="22" viewBox="0 0 22 22"><path d="M19 9.5A8 8 0 1 1 14.5 3.8" fill="none" stroke="#fff" stroke-width="2"/><path d="M7 10.5l3.5 3.5L19.5 4.5" fill="none" stroke="#fff" stroke-width="2.2"/></svg><span>Sie sind daran interessiert, Teil unseres Vertriebsnetzwerks zu werden</span></li>
      <li><svg width="22" height="22" viewBox="0 0 22 22"><path d="M19 9.5A8 8 0 1 1 14.5 3.8" fill="none" stroke="#fff" stroke-width="2"/><path d="M7 10.5l3.5 3.5L19.5 4.5" fill="none" stroke="#fff" stroke-width="2.2"/></svg><span>Sie möchten sich ein passives Einkommen sichern</span></li>
      <li><svg width="22" height="22" viewBox="0 0 22 22"><path d="M19 9.5A8 8 0 1 1 14.5 3.8" fill="none" stroke="#fff" stroke-width="2"/><path d="M7 10.5l3.5 3.5L19.5 4.5" fill="none" stroke="#fff" stroke-width="2.2"/></svg><span>Sie sind an den Chancen und neuen Möglichkeiten des Krypto-Marktes interessiert</span></li>
    </ul>
  </section>

  <footer class="abs footer"></footer>
</body>
</html>
```